Web Developer Needs a Business Card Design

I need a personal business card design that represents me as a web developer for potential employers. I would like the background to be a dark color on the front for contrast with my logo and name. The back will have all my information along with a smaller version of the logo. I want something with a modern look and feel, not too conservative. This will be used for potential employers and freelance work.

Industry/Entity Type

Business

Contact Information for Business Card

Front should have my logo and name. The back should have all my personal information which would include: name: Tom Varulek, phone: 570-614-3098, email: tomvarulek@quillbox.net, website url: www.tomvarulek.net, logo, web developer.

Font styles to use
Sans Serif

Requirements
Must have
• Must include my logo. The color palette base color will be the logo color.

```html
<!DOCTYPE html>
<html lang="en">
<head>
<meta charset="UTF-8">
<title>Tom Varulek — Business Card</title>
<link rel="stylesheet" href="https://fonts.googleapis.com/css2?family=Roboto:wght@400;500&display=swap">
<style>
  :root {
    --page: #dcdcdc;
    --card: #070707;
    --card-glow: #1b1d1e;
    --mint: #52e6bd;
    --shadow: rgba(0, 0, 0, 0.35);
  }
  * { box-sizing: border-box; margin: 0; padding: 0; }
  html, body {
    width: 1200px;
    height: 1200px;
    overflow: hidden;
  }
  body {
    background: radial-gradient(circle at 50% 45%, #ececec 0%, var(--page) 70%, #cfcfcf 100%);
    font-family: "Roboto", Arial, sans-serif;
    position: relative;
  }
  .card {
    position: absolute;
    left: 285px;
    width: 630px;
    height: 360px;
    border-radius: 22px;
    background: var(--card);
    overflow: hidden;
    box-shadow: 0 14px 30px var(--shadow);
  }
  .card--front { top: 200px; }
  .card--back { top: 640px; }
  .card__ambience {
    position: absolute;
    inset: 0;
    background:
      radial-gradient(ellipse at 85% 10%, #232527 0%, transparent 45%),
      linear-gradient(105deg, transparent 30%, var(--card-glow) 42%, transparent 55%);
    opacity: 0.8;
  }
  .brand {
    position: absolute;
    display: flex;
    align-items: center;
    gap: 16px;
    color: var(--mint);
    font-weight: 500;
  }
  .brand__circle {
    border: 6px solid var(--mint);
    border-radius: 50%;
    flex-shrink: 0;
  }
  .card--front .brand {
    left: 50%;
    top: 50%;
    transform: translate(-50%, -50%);
    font-size: 34px;
  }
  .card--front .brand__circle { width: 64px; height: 64px; }
  .card--back .brand {
    left: 44px;
    top: 50%;
    transform: translateY(-50%);
    font-size: 22px;
  }
  .card--back .brand__circle { width: 44px; height: 44px; border-width: 5px; }
  .details {
    position: absolute;
    left: 348px;
    top: 108px;
    color: var(--mint);
  }
  .details__name {
    font-size: 28px;
    font-weight: 400;
    letter-spacing: 0.5px;
  }
  .details__role {
    font-size: 15px;
    margin-top: 4px;
    margin-left: 22px;
  }
  .contact {
    list-style: none;
    margin-top: 34px;
    margin-left: 44px;
  }
  .contact__item {
    display: flex;
    align-items: center;
    gap: 14px;
    font-size: 16px;
    line-height: 28px;
  }
  .contact__icon {
    width: 14px;
    height: 14px;
    fill: var(--mint);
    stroke: var(--mint);
  }
</style>
</head>
<body>
  <section class="card card--front">
    <div class="card__ambience" role="img" aria-label="Dim photo of a dark workspace behind the card face"></div>
    <div class="brand">
      <span class="brand__circle"></span>
      <span class="brand__name">Tom Varulek</span>
    </div>
  </section>

  <section class="card card--back">
    <div class="card__ambience" role="img" aria-label="Dim photo of a dark workspace behind the card face"></div>
    <div class="brand">
      <span class="brand__circle"></span>
      <span class="brand__name">Tom Varulek</span>
    </div>
    <div class="details">
      <h1 class="details__name">Tom Varulek</h1>
      <p class="details__role">Web Developer</p>
      <ul class="contact">
        <li class="contact__item">
          <svg class="contact__icon" viewBox="0 0 14 14" stroke-width="0"><path d="M1 4c0-2 2-3 6-3s6 1 6 3v1h-3V4H4v1H1zM3 6h8l2 6H1z"/></svg>
          <span>570-614-3098</span>
        </li>
        <li class="contact__item">
          <svg class="contact__icon" viewBox="0 0 14 14" stroke-width="0"><path d="M0 3h14v9H0zM1 4l6 4 6-4v-.1L7 7 1 3.9z" fill-rule="evenodd"/></svg>
          <span>tomvarulek@quillbox.net</span>
        </li>
        <li class="contact__item">
          <svg class="contact__icon" viewBox="0 0 14 14" fill="none" stroke-width="1.4"><circle cx="7" cy="7" r="5.8"/><ellipse cx="7" cy="7" rx="2.4" ry="5.8"/><path d="M1.2 7h11.6"/></svg>
          <span>www.tomvarulek.net</span>
        </li>
      </ul>
    </div>
  </section>
</body>
</html>
```